Business Card and Letterhead for Pimlu - modern real estate business

I need a double sided business card design for Pimlu. Please see business card brief here https://files.trelvonadocs.com/sheet/r/7QzTmWbaXLJnoPEd-kRyUgFhHsstbvCe2qfoMxDa_pz/view?mode=shared

Please feel free to design the business cards however you feel best. I am happy to give some creative freedoms and then provide feedback from there.

Please then also create a letterhead to match the business card design

Colors

Designer to choose colors to be used in the design.

Requirements
Must have
• Must be a modern, elegant business card which looks very professional

```html
<!DOCTYPE html>
<html lang="en">
<head>
<meta charset="utf-8">
<title>Pimlu Letterhead</title>
<link rel="stylesheet" href="https://fonts.googleapis.com/css2?family=Roboto:wght@400;500;700&display=swap">
<style>
  :root {
    --brand-red: #e31e24;
    --ink: #1d1d1f;
    --paper: #ffffff;
    --backdrop: #d9dae0;
  }
  * { margin: 0; padding: 0; box-sizing: border-box; }
  html, body {
    width: 1200px;
    height: 899px;
    overflow: hidden;
    background: var(--backdrop);
    font-family: "Roboto", Arial, sans-serif;
  }
  .letterhead {
    position: absolute;
    left: 350px;
    top: 96px;
    width: 506px;
    height: 714px;
    background: var(--paper);
  }
  .brand-name {
    position: absolute;
    left: 22px;
    top: 54px;
    font-size: 30px;
    font-weight: 700;
    letter-spacing: 1px;
    line-height: 1;
    color: var(--brand-red);
    text-transform: uppercase;
  }
  .contact-list {
    position: absolute;
    left: 406px;
    top: 31px;
    list-style: none;
    font-size: 9px;
    line-height: 13.5px;
    color: var(--ink);
  }
  .contact-list li {
    display: flex;
    align-items: center;
    gap: 5px;
    white-space: nowrap;
  }
  .contact-label { color: var(--brand-red); }
  .contact-icon { width: 7px; height: 7px; flex: none; fill: var(--brand-red); }
  .header-rule {
    position: absolute;
    left: 22px;
    top: 89px;
    width: 463px;
    height: 1.5px;
    background: var(--brand-red);
  }
  .footer-band {
    position: absolute;
    left: 22px;
    top: 683px;
    width: 463px;
    height: 12px;
    background: var(--brand-red);
    color: var(--paper);
    font-size: 8.5px;
    line-height: 12px;
    text-align: center;
  }
</style>
</head>
<body>
  <main class="letterhead">
    <div class="brand-name">Pimlu</div>

    <ul class="contact-list">
      <li><span><span class="contact-label">Lic No.</span> 20480316</span></li>
      <li>
        <svg class="contact-icon" viewBox="0 0 10 10" aria-hidden="true"><path d="M2 0.5 L3.6 0.5 L4.3 2.8 L3.1 3.7 Q4.1 5.9 6.3 6.9 L7.2 5.7 L9.5 6.4 L9.5 8 Q9.5 9.5 8 9.5 Q0.5 9 0.5 2 Q0.5 0.5 2 0.5 Z"/></svg>
        <span>02 5550 3817</span>
      </li>
      <li>
        <svg class="contact-icon" viewBox="0 0 10 10" aria-hidden="true"><path d="M0.5 2 H9.5 V8.5 H0.5 Z M1.2 2.6 L5 5.4 L8.8 2.6 Z" fill-rule="evenodd"/></svg>
        <span>info@pimlu.com</span>
      </li>
      <li>
        <svg class="contact-icon" viewBox="0 0 10 10" aria-hidden="true"><circle cx="5" cy="5" r="4.5"/><path d="M0.8 5 H9.2 M5 0.6 Q2.6 5 5 9.4 M5 0.6 Q7.4 5 5 9.4" stroke="#fff" stroke-width="0.8" fill="none"/></svg>
        <span>www.pimlu.com</span>
      </li>
    </ul>

    <div class="header-rule"></div>

    <footer class="footer-band">PO Box 1187 Harlow Vale NSW 2790</footer>
  </main>
</body>
</html>
```